Accountant website

Please design a accountant website for www.fenwaybridgeadvisory.com.au. This site is majorly out of date, and is not supported by modern browsers.

The style should use the reds from the design at dev.fenwaybridgeadvisory.com.au, and should be modern and make use of Slides (large content slides that the user scrolls through on the front page).

The content is largely already on the site, however happy to move some around to suit the modern design as required.

The dev.fenwaybridgeadvisory.com.au was a rough mock up that I have completed that the client is "happy" with the direction, however this needs a lot of polish and finishing touches, and I will accept designs that differ from this, but highly recommend that this is used as a guide.

Ready to be sliced PSD Only - HTML no required.

In all honesty, although I can technically do a lot of this, the polished finished I want for this site has eluded me in a few attempts, and therefore I am looking out there at you much more artistic people to finish (or redesign if required) this site.

Target Market(s)

Higher end Small - Medium Business

Industry/Entity Type

Accountant

Requirements
Must have
• Must use the logo from dev.fenwaybridgeadvisory.com.au use exactly the red colours as defined in this layout. A basic layout PSD (to get the colour etc) and the logo in ai format is attached to this project. Please ignore the SSL warning on the development site.

The final product does NOT have to be the same as shown on dev.fenwaybridgeadvisory.com.au however the red colour scheme must be used. The client DOES want the logo on the RIGHT.

Must have a front landing page design, and a page layout that considers the other page content (at least one separate PSD)
Nice to have
• I really am looking at a slide format for the front page simular to:

http://www.quillo.com/au/
http://www.vaultmoor.com/

The attached photos should be used on the site. Was considering a rotating banner with these images are a watermark background on a solid Red header bar, but happy to be shown other options.
Should not have
• Please no "Layout Goblin" submissions.

```html
<!DOCTYPE html>
<html lang="en">
<head>
<meta charset="utf-8">
<title>Fenway Bridge Advisory</title>
<link href="https://fonts.googleapis.com/css2?family=PT+Sans:ital,wght@0,400;0,700;1,400&family=Roboto+Condensed:wght@400;500&display=swap" rel="stylesheet">
<style>
:root{
  --red:#9e2b2f;
  --red-nav:#a3302f;
  --red-active:#85231f;
  --red-light:#b33a3c;
  --text:#6b6b6b;
  --text-dark:#333;
  --rule:#dcdcdc;
  --white:#fff;
}
*{box-sizing:border-box;margin:0;padding:0}
html,body{width:1110px;height:1200px;overflow:hidden;background:var(--white);font-family:"PT Sans",sans-serif;color:var(--text)}
.page{position:relative;width:1110px;height:1200px}
.topbar{position:absolute;left:0;top:0;width:1110px;height:63px;background:linear-gradient(#fff,#f1f1f1)}
.follow{position:absolute;left:166px;top:22px;display:flex;align-items:center;gap:4px;font-size:8px;color:#555;letter-spacing:.2px}
.follow .dot{width:22px;height:22px;border-radius:50%;background:#b8b8b8;margin-left:2px}
.brand{position:absolute;right:170px;top:14px;text-align:left;color:var(--text-dark)}
.brand-name{font-weight:700;font-size:19px;line-height:18px;letter-spacing:-.3px}
.brand-sub{font-size:8px;letter-spacing:.2px}
.brand-mark{position:absolute;right:-30px;top:2px;width:22px;height:22px;background:var(--red)}
.nav{position:absolute;left:0;top:63px;width:1110px;height:34px;background:var(--red-nav);display:flex;padding-left:166px}
.nav a{color:var(--white);text-decoration:none;font-size:10px;font-weight:700;line-height:34px;padding:0 28px;white-space:nowrap}
.nav a.active{background:var(--red-active);padding:0 34px 0 36px}
.hero{position:absolute;left:0;top:97px;width:1110px;height:381px;background:linear-gradient(90deg,#c9d3dc 0%,#aeb9c2 35%,#9aa7b0 60%,#8a5a4c 78%,#b8443f 88%,#7a7a6a 100%)}
.hero-title{position:absolute;left:184px;top:88px;font-family:"Roboto Condensed",sans-serif;color:var(--white);line-height:1}
.hero-title .l1{font-size:56px;font-weight:500}
.hero-title .l2{font-size:40px;font-weight:500;margin-top:4px}
.hero-title .l3{font-size:23px;font-weight:500;color:#1e1e1e;margin-top:8px}
.btn-login{position:absolute;left:186px;top:242px;width:158px;height:42px;background:var(--red-light);color:var(--white);font-family:"Roboto Condensed",sans-serif;font-size:17px;display:flex;align-items:center;justify-content:center;gap:8px}
.hero-arrow{position:absolute;top:178px;width:32px;height:30px;background:rgba(160,60,60,.25)}
.welcome{position:absolute;left:0;top:478px;width:1110px;height:70px;background:linear-gradient(#ececec,#fff)}
.welcome-title{position:absolute;top:508px;width:1110px;text-align:center;color:var(--red);font-size:24px}
.welcome-text{position:absolute;top:547px;left:180px;width:750px;text-align:center;font-size:9.6px;line-height:17.5px}
h2{position:absolute;font-weight:400;color:var(--red);font-size:21px}
.team-photo{position:absolute;left:166px;top:658px;width:373px;height:138px;background:linear-gradient(90deg,#8e2a2c,#b6343a 45%,#c9c9c9 70%,#9e2b2f)}
.body-text{position:absolute;left:166px;width:380px;font-size:8.4px;line-height:14.4px}
.btn{position:absolute;height:27px;background:var(--red);color:var(--white);font-size:8.6px;line-height:27px;text-align:center;border-radius:2px}
.t-arrows{position:absolute;left:536px;top:968px;display:flex;gap:6px}
.testimonial{position:absolute;top:1002px;width:190px}
.testimonial .who{color:var(--red);font-size:8.4px;line-height:14.4px}
.testimonial .quote{font-style:italic;font-size:8.2px;line-height:14.4px;margin-top:8px}
.testimonial .more{color:var(--red);font-size:8.4px;margin-top:6px}
.t-divider{position:absolute;left:364px;top:1003px;width:1px;height:84px;background:var(--rule)}
.article{position:absolute;left:588px;width:340px}
.article .icon{position:absolute;left:0;top:0;width:34px;height:34px;border-radius:50%;background:var(--red)}
.article .title{position:absolute;left:45px;top:5px;color:var(--red);font-size:12.5px;white-space:nowrap}
.article .summary{position:absolute;left:48px;top:30px;width:280px;font-size:8.2px;line-height:14.3px}
.article .comments{position:absolute;left:48px;top:98px;font-size:8px;font-style:italic;color:var(--red);display:flex;align-items:center;gap:5px}
.article-rule{position:absolute;left:633px;width:295px;height:1px;background:var(--rule)}
.footer{position:absolute;left:0;top:1128px;width:1110px;height:72px;background:var(--red)}
.footer-links{position:absolute;left:168px;top:19px;display:flex;font-size:7.4px;color:var(--white)}
.footer-links span{padding:0 8px;border-left:1px solid rgba(255,255,255,.8);line-height:9px}
.footer-links span:first-child{padding-left:0;border-left:0}
.copyright{position:absolute;left:168px;top:42px;font-size:7.2px;color:var(--white)}
.partner-badge{position:absolute;left:804px;top:14px;width:44px;height:44px;border-radius:50%;background:var(--white)}
.partner-shape{position:absolute;left:860px;top:22px;width:80px;height:28px;background:rgba(255,255,255,.85);border-radius:2px}
</style>
</head>
<body>
<div class="page">
  <header class="topbar">
    <div class="follow">FOLLOW US :<span class="dot"></span><span class="dot"></span><span class="dot"></span><span class="dot"></span></div>
    <div class="brand"><div class="brand-name">FENWAY BRIDGE</div><div class="brand-sub">ADVISORY</div><span class="brand-mark"></span></div>
  </header>
  <nav class="nav">
    <a class="active">ABOUT US</a><a>SERVICES</a><a>WORKING WITH US</a><a>TESTIMONIALS</a><a>NEWS</a><a>ARTICLE OF THE MOMENT ARCHIVE</a>
  </nav>

  <section class="hero" role="img" aria-label="Smiling adviser in a red top at a sunny marina with blurred yachts behind">
    <div class="hero-arrow" style="left:92px"></div>
    <div class="hero-arrow" style="left:994px"></div>
    <div class="hero-title">
      <div class="l1">FENWAY BRIDGE</div>
      <div class="l2">ADVISORY</div>
      <div class="l3">GETTING TO KNOW FENWAY BRIDGE ADVISORY</div>
    </div>
    <div class="btn-login">CLIENT LOGIN
      <svg width="12" height="14" viewBox="0 0 12 14"><path d="M1 1l5 6-5 6M6 1l5 6-5 6" fill="none" stroke="#fff" stroke-width="1.6"/></svg>
    </div>
  </section>

  <div class="welcome"></div>
  <div class="welcome-title">Welcome to Fenway Bridge</div>
  <p class="welcome-text">Fenway Bridge Advisory aims to service the needs of its clients by focusing on the present rather than reporting on historical figures. We recognise that business owners benefit from regular contact with their accountant. One who undertakes a hands on approach in working with business owners to improve their business.</p>

  <h2 style="left:166px;top:616px">Fenway Bridge Advisory Difference</h2>
  <div class="team-photo" role="img" aria-label="Four team members seated at the reception desk in front of a red wall"></div>
  <p class="body-text" style="top:816px">Not all Accountants are created equally … the Fenway Bridge Advisory difference Fenway Bridge Advisory takes pride in not following the status quo, the following points are just some of the unique benefits you will experience when working with us.</p>
  <p class="body-text" style="top:873px">Believing in the here and now: A proactive accountant that focuses on providing timely and relevant information.</p>
  <div class="btn" style="left:166px;top:915px;width:102px">READ MORE INFO</div>

  <h2 style="left:166px;top:962px">Testimonials</h2>
  <div class="t-arrows">
    <svg width="6" height="9" viewBox="0 0 6 9"><path d="M5 1L1 4.5 5 8" fill="none" stroke="#999" stroke-width="1.3"/></svg>
    <svg width="6" height="9" viewBox="0 0 6 9"><path d="M1 1l4 3.5L1 8" fill="none" stroke="#999" stroke-width="1.3"/></svg>
  </div>
  <div class="testimonial" style="left:167px">
    <div class="who">JOAN WHITCOMBE FROM BRIGHTLINE ELECTRICAL SUPPLIES PTY LTD</div>
    <div class="quote">We have been using Fenway Bridge Advisory since 2007, and have always found Rosalind &amp; her staff to give high quality, effective service.</div>
    <div class="more">[ Read More ]</div>
  </div>
  <div class="t-divider"></div>
  <div class="testimonial" style="left:381px">
    <div class="who">JOAN WHITCOMBE FROM BRIGHTLINE ELECTRICAL SUPPLIES PTY LTD</div>
    <div class="quote">We have been using Fenway Bridge Advisory since 2007, and have always found Rosalind &amp; her staff to give high quality, effective service.</div>
    <div class="more">[ Read More ]</div>
  </div>

  <h2 style="left:587px;top:616px">Articles of the Moment</h2>

  <article class="article" style="top:664px">
    <span class="icon"><svg width="34" height="34" viewBox="0 0 34 34"><path d="M13 11l6 6-6 6M18 11l6 6-6 6" fill="none" stroke="#fff" stroke-width="1.6"/></svg></span>
    <div class="title">When First Impressions Count...</div>
    <p class="summary">I attended a local solicitors' office this morning and upon arriving was immediately impressed with the appearance of the reception and waiting area. The receptionist greeted me warmly and instructed ...<br>Full story</p>
    <div class="comments"><svg width="10" height="8" viewBox="0 0 10 8"><path d="M0 0h10v6H3L1 8V6H0z" fill="#999"/></svg>Comments (3)</div>
  </article>
  <div class="article-rule" style="top:782px"></div>

  <article class="article" style="top:791px">
    <span class="icon"><svg width="34" height="34" viewBox="0 0 34 34"><path d="M13 11l6 6-6 6M18 11l6 6-6 6" fill="none" stroke="#fff" stroke-width="1.6"/></svg></span>
    <div class="title">6 Tips for Naming your Business</div>
    <p class="summary">I attended a local solicitors' office this morning and upon arriving was immediately impressed with the appearance of the reception and waiting area. The receptionist greeted me warmly and instructed ...<br>Full story</p>
    <div class="comments"><svg width="10" height="8" viewBox="0 0 10 8"><path d="M0 0h10v6H3L1 8V6H0z" fill="#999"/></svg>Comments (3)</div>
  </article>
  <div class="article-rule" style="top:909px"></div>

  <article class="article" style="top:917px">
    <span class="icon"><svg width="34" height="34" viewBox="0 0 34 34"><path d="M13 11l6 6-6 6M18 11l6 6-6 6" fill="none" stroke="#fff" stroke-width="1.6"/></svg></span>
    <div class="title">Energy Efficiency</div>
    <p class="summary">I attended a local solicitors' office this morning and upon arriving was immediately impressed with the appearance of the reception and waiting area. The receptionist greeted me warmly and instructed ...<br>Full story</p>
    <div class="comments"><svg width="10" height="8" viewBox="0 0 10 8"><path d="M0 0h10v6H3L1 8V6H0z" fill="#999"/></svg>Comments (3)</div>
  </article>
  <div class="btn" style="left:636px;top:1043px;width:149px">VIEW ALL ARCHIVED ARTICLES</div>

  <footer class="footer">
    <div class="footer-links"><span>HOME</span><span>ABOUT US</span><span>SERVICES</span><span>WORKING WITH US</span><span>LINKS</span><span>TESTIMONIALS</span><span>NEWS</span><span>ARTICLE OF THE MOMENT ARCHIVE</span><span>CONTACT US</span></div>
    <div class="copyright">COPYRIGHT © 2013. FENWAY BRIDGE ADVISORY. ALL RIGHTS RESERVED.</div>
    <div class="partner-badge"></div>
    <div class="partner-shape"></div>
  </footer>
</div>
</body>
</html>
```